Simple but elegant business card/logo design for exclusive beauty business

We need a logo designed for a new elegant and exclusive beauty business called "G". The logo itself should be a stylistic and custom design for the letter "G". We would like the business card to have the logo as the centrepiece on a clean background. Gold Logo on black background or silver on white background.

The business card details should be displayed centre of the card. Details are as follows:

Marla Vance
Facebook: /simplyshinebym
Instagram: /simplyshinebym

The words "Simply Shine" should also appear somewhere on the card.

Industry/Entity Type

Business

Logo Text

G

Requirements
Must have
• Design must be simple, clean and elegant
Should not have
• The design should not be cluttered

```html
<!DOCTYPE html>
<html lang="en">
<head>
<meta charset="utf-8">
<title>Simply Shine by M — Business Card</title>
<link rel="stylesheet" href="https://fonts.googleapis.com/css2?family=Montserrat:wght@400;500;600;700&display=swap">
<style>
  :root {
    --backdrop: #2a2a2a;
    --card: #141414;
    --card-edge: #1e1e1e;
    --gold: #c99a3e;
    --gold-light: #e4bf6a;
    --gold-fade: rgba(201, 154, 62, 0);
    --pattern-tone: rgba(120, 100, 70, 0.22);
  }
  * { margin: 0; padding: 0; box-sizing: border-box; }
  html, body {
    width: 1200px;
    height: 660px;
    overflow: hidden;
    background: var(--backdrop);
    font-family: "Montserrat", sans-serif;
  }
  .canvas {
    width: 1200px;
    height: 660px;
    display: flex;
    align-items: center;
    justify-content: center;
    gap: 40px;
  }
  .card {
    width: 520px;
    height: 300px;
    background: var(--card);
    border: 1px solid var(--card-edge);
    border-radius: 3px;
    position: relative;
    overflow: hidden;
  }

  /* Front: faint brand pattern behind a centred brand name */
  .card-front {
    display: flex;
    align-items: center;
    justify-content: center;
  }
  .brand-pattern {
    position: absolute;
    inset: 0;
    background:
      radial-gradient(ellipse 30% 55% at 18% 60%, var(--pattern-tone), transparent 70%),
      radial-gradient(ellipse 28% 50% at 78% 35%, var(--pattern-tone), transparent 70%),
      radial-gradient(ellipse 22% 40% at 45% 15%, var(--pattern-tone), transparent 70%);
  }
  .front-brand {
    position: relative;
    color: var(--gold);
    font-weight: 600;
    font-size: 28px;
    line-height: 1.15;
    text-align: center;
  }

  /* Back: brand left, details right */
  .card-back {
    display: flex;
    align-items: center;
  }
  .back-brand {
    width: 270px;
    padding-left: 50px;
    color: var(--gold);
    font-weight: 600;
    font-size: 24px;
    line-height: 1.1;
    padding-top: 70px;
  }
  .divider {
    width: 2px;
    height: 150px;
    background: linear-gradient(to bottom, var(--gold-fade), var(--gold-light) 50%, var(--gold-fade));
  }
  .details {
    padding-left: 26px;
    padding-bottom: 40px;
    color: var(--gold);
  }
  .holder-name {
    font-size: 17px;
    margin-bottom: 12px;
    font-weight: 400;
  }
  .holder-name strong { font-weight: 700; }
  .contact-list { list-style: none; }
  .contact-list li {
    display: flex;
    align-items: center;
    gap: 8px;
    font-size: 11px;
    font-weight: 500;
    line-height: 1;
    margin-bottom: 7px;
  }
  .contact-list li.group-gap { margin-top: 10px; }
  .icon {
    width: 11px;
    height: 11px;
    flex: none;
  }
  .social-square {
    width: 10px;
    height: 10px;
    background: var(--gold);
    border-radius: 1px;
    flex: none;
  }
</style>
</head>
<body>
  <main class="canvas">
    <section class="card card-front" aria-label="Card front">
      <div class="brand-pattern" role="img" aria-label="Faint repeated brand symbol pattern in dark bronze"></div>
      <p class="front-brand">Simply Shine<br>by M</p>
    </section>

    <section class="card card-back" aria-label="Card back">
      <p class="back-brand">Simply Shine<br>by M</p>
      <div class="divider"></div>
      <div class="details">
        <p class="holder-name"><strong>Marla</strong> Vance</p>
        <ul class="contact-list">
          <li>
            <svg class="icon" viewBox="0 0 12 12" aria-hidden="true">
              <rect x="3" y="0.5" width="6" height="11" rx="1" fill="none" stroke="#c99a3e" stroke-width="1.2"/>
              <circle cx="6" cy="9.5" r="0.7" fill="#c99a3e"/>
            </svg>
            0400 517 293
          </li>
          <li>
            <svg class="icon" viewBox="0 0 12 12" aria-hidden="true">
              <rect x="0.6" y="2" width="10.8" height="8" fill="none" stroke="#c99a3e" stroke-width="1.2"/>
              <path d="M0.6 2 L6 6.5 L11.4 2" fill="none" stroke="#c99a3e" stroke-width="1.2"/>
            </svg>
            hello@simplyshinebym.com
          </li>
          <li class="group-gap"><span class="social-square"></span>/simplyshinebym</li>
          <li><span class="social-square"></span>/simplyshinebym</li>
        </ul>
      </div>
    </section>
  </main>
</body>
</html>
```